Large online photo magazine needs redesign

We have previously digitised a historical photographic magazine of around 20,000 printed pages and made it available online. The magazine ran up to the early 1970s, and the content is largely black and white photographs of local events, accompanied by short captions.

Although the content is very rich, the design needs to be revisited so that:
* it is visually appealing
* it is responsive (i.e. works in browsers across all manner of devices)
* is faithful to the nature of the content

There are only a few core page types, and the central one is the article page, an example of which can be seen at:
http://snapgazette.example/gisborne/issue/KLR48_19600714/t1-body-d4.html

Any design submitted should be based on the treatment of an article page such as the above.

Given the large number of pages on our site, we need a design which can be templated to work for any content in the collection, i.e. we cannot hand-craft our templates to match a given page of content, rather a template must work acceptably well for all content.

The current site, although basic in design, has the advantage that it is quite efficient in the amount of data per page request (around 100k - 200k). While not adverse to web fonts, banner imagery etc, we will carefully consider the benefit gained from any such treatment against the amount of extra data that needs to be downloaded to the client's browser.

For the right design, we are able ourselves to adapt it to a CSS layout.

An example of each core page type is as follows (though for this project we only expect a design for a single page, as itemised above):

http://snapgazette.example/gisborne/index.html
http://snapgazette.example/gisborne/about.html
http://snapgazette.example/gisborne/help.html
http://snapgazette.example/gisborne/initial/index.html
http://snapgazette.example/gisborne/search/results?type=section&text=smith&cmdSubmit=Go
http://snapgazette.example/gisborne/advanced-search/index.html
http://snapgazette.example/gisborne/issue/KLR48_19600714/t1-front-d1.html
http://snapgazette.example/gisborne/issue/KLR48_19600714/index.html
http://snapgazette.example/gisborne/issue/KLR48_19600714/fig-KLR48_19600714_005a.html
http://snapgazette.example/gisborne/issue/KLR48_19600714/KLR48_19600714_012.html
http://snapgazette.example/gisborne/issue/KLR48_19600714/thumbnails.html

Target Market(s)

A general browsing audience of all ages, but skewed towards the older generations, and those interested in family / regional history.

The average user will not be particularly web-savy, and the treatment of the content should not detract / distract from the actual content itself.

Industry/Entity Type

Events

Requirements
Must have
• * it is visually appealing
The content should be visually appealing to the audience, which can be defined as a general browsing audience of all ages, but skewed towards the middle and older generations.

* it is responsive (the design can be adapted - by us - to work in browsers across all manner of devices)

The magazine covers (http://snapgazette.example/gisborne/issues/index.html) offer some possible inspiration for treatment of the material.

```html
<!DOCTYPE html>
<html lang="en">
<head>
<meta charset="utf-8">
<title>Snap Gazette – Flying Sisters from Gisborne</title>
<link rel="stylesheet" href="https://fonts.googleapis.com/css2?family=Open+Sans:wght@400;600;700&display=swap">
<style>
:root{
  --brand-red:#cf3c55;
  --accent-red:#d0425a;
  --nav-black:#000;
  --page-grey:#f3f3f3;
  --paper:#fff;
  --text:#333;
  --side-tab:#e4e2b6;
  --button:#e4e4e4;
  --footer:#2b2b2b;
  --social-blue:#1b5aa6;
  --social-light:#4aa3e0;
}
*{box-sizing:border-box;margin:0;padding:0}
html,body{width:1125px;height:1200px;overflow:hidden}
body{font-family:"Open Sans",sans-serif;color:var(--text);background:var(--page-grey);position:relative}
a{color:inherit;text-decoration:none}

.masthead{position:absolute;left:0;top:0;width:1125px;height:93px;background:var(--brand-red)}
.brand{position:absolute;left:180px;top:28px;display:flex;align-items:center;gap:10px;color:#fff;font-weight:700;font-size:30px;letter-spacing:.5px}
.brand-mark{width:22px;height:22px;background:#fff}
.search{position:absolute;left:561px;top:30px;width:316px;height:31px;background:#fff}
.search svg{position:absolute;right:8px;top:3px}
.advanced-link{position:absolute;left:572px;top:64px;color:#fff;font-size:13.5px;font-weight:600;text-decoration:underline}

.main-nav{position:absolute;left:0;top:93px;width:1125px;height:69px;background:var(--nav-black)}
.main-nav a{position:absolute;top:27px;color:#fff;font-size:14.5px}

.page{position:absolute;left:163px;top:162px;width:767px;height:936px;background:var(--paper)}
.breadcrumb{position:absolute;left:176px;top:173px;font-size:14px;color:#555}
.breadcrumb .current{color:var(--accent-red)}
.breadcrumb-rule{position:absolute;left:166px;top:195px;width:764px;height:1.5px;background:#444}

.side-tab{position:absolute;left:171px;width:126px;height:27px;background:var(--side-tab);font-size:11px;padding:6px 7px;display:flex;justify-content:space-between}

.article-btn{position:absolute;top:224px;height:28px;background:var(--button);font-size:9px;display:flex;align-items:center;justify-content:center;gap:4px;color:#222}

.photo{position:absolute;left:371px;top:257px;width:415px;height:464px;background:linear-gradient(160deg,#d9d5b8,#8c8a78 45%,#ebe8d4)}
.round-arrow{position:absolute;top:467px;width:42px;height:42px;border-radius:50%;background:#ddd;display:flex;align-items:center;justify-content:center}

.article-date{position:absolute;left:373px;top:733px;color:var(--accent-red);font-size:14px}
.issue-no{position:absolute;left:742px;top:730px;color:var(--accent-red);font-size:13.5px;font-weight:700}
.article-title{position:absolute;left:374px;top:761px;color:var(--accent-red);font-size:14.5px;font-weight:400}
.article-body{position:absolute;left:372px;top:794px;width:440px;font-size:14px;line-height:22.5px}

.more-heading{position:absolute;left:376px;top:905px;font-size:18px;font-weight:400;color:#222}
.thumb{position:absolute;border:1px solid #222;padding:2px;background:#fff}
.thumb span{display:block;width:100%;height:100%}
.small-arrow{position:absolute;top:976px;width:23px;height:23px;border-radius:50%;background:#ddd;display:flex;align-items:center;justify-content:center}

.site-footer{position:absolute;left:0;top:1098px;width:1125px;height:102px;background:var(--footer)}
.social-link{position:absolute;display:flex;align-items:center;gap:9px;font-weight:600;font-size:22px}
.social-link i{display:block;width:14px;height:14px}
.social-link.friendbook{left:180px;top:1050px;color:var(--social-blue)}
.social-link.friendbook i{background:var(--social-blue)}
.like-us{position:absolute;left:204px;top:1128px;color:#8fb4e0;font-size:16px}
.social-link.chirper{left:800px;top:1060px;color:var(--social-blue)}
.social-link.chirper i{border-radius:50%;background:var(--social-light)}
.licence-badge{position:absolute;left:513px;top:1130px;width:67px;height:23px;background:#ccc;border:1px solid #000}
.copyright{position:absolute;left:0;top:1162px;width:1097px;text-align:center;color:#ccc;font-size:13.5px}
</style>
</head>
<body>

<header class="masthead">
  <a class="brand" href="http://snapgazette.example/gisborne/index.html"><span class="brand-mark"></span>SNAP GAZETTE</a>
  <div class="search" role="search">
    <svg width="26" height="26" viewBox="0 0 26 26"><circle cx="11" cy="11" r="8" fill="none" stroke="#000" stroke-width="2.6"/><line x1="17" y1="17" x2="24" y2="24" stroke="#000" stroke-width="3"/></svg>
  </div>
  <a class="advanced-link" href="http://snapgazette.example/gisborne/advanced-search/index.html">Advance Search +</a>
</header>

<nav class="main-nav">
  <a style="left:187px" href="http://snapgazette.example/gisborne/index.html">Home</a>
  <a style="left:274px" href="http://snapgazette.example/gisborne/about.html">About</a>
  <a style="left:369px" href="http://snapgazette.example/gisborne/issues/index.html">Browse Snap Gazette</a>
  <a style="left:622px" href="http://snapgazette.example/gisborne/initial/index.html">A-Z people</a>
  <a style="left:742px" href="http://snapgazette.example/gisborne/help.html">Help</a>
  <a style="left:824px" href="#">Report an error</a>
</nav>

<main class="page"></main>
<div class="breadcrumb">Snap Gazette \ Issues \ KLR48_19600714 \ <span class="current">t1-body-d4</span></div>
<div class="breadcrumb-rule"></div>

<div class="side-tab" style="top:229px"><span>Category</span><span>+</span></div>
<div class="side-tab" style="top:258px"><span>Recent views</span><span>+</span></div>

<a class="article-btn" style="left:407px;width:95px" href="#">‹ Previous article</a>
<a class="article-btn" style="left:510px;width:78px" href="#">Next article ›</a>
<a class="article-btn" style="left:606px;width:78px" href="http://snapgazette.example/gisborne/issue/KLR48_19600714/index.html">Issue content</a>
<a class="article-btn" style="left:691px;width:95px" href="#">
  <svg width="16" height="14" viewBox="0 0 16 14"><rect x="4" y="1" width="8" height="4" fill="#fff" stroke="#777"/><rect x="1" y="5" width="14" height="6" fill="#aaa"/><rect x="4" y="9" width="8" height="4" fill="#fff" stroke="#777"/></svg>Print this article</a>

<div class="photo" role="img" aria-label="Scanned black and white magazine photograph of three air hostesses in uniform caps, with a printed caption beneath"></div>
<div class="round-arrow" style="left:316px"><svg width="14" height="18" viewBox="0 0 14 18"><polyline points="11,2 4,9 11,16" fill="none" stroke="#000" stroke-width="3.5"/></svg></div>
<div class="round-arrow" style="left:795px"><svg width="14" height="18" viewBox="0 0 14 18"><polyline points="3,2 10,9 3,16" fill="none" stroke="#000" stroke-width="3.5"/></svg></div>

<div class="article-date">July 14, 1960</div>
<div class="issue-no">No 73</div>
<h1 class="article-title">Flying Sisters from Gisborne</h1>
<p class="article-body">This is probably something of a record--three sisters who are all air hostesses. They are the Hartley sisters.....Marguerite, Elspeth, and Rosalind, daughters of Mr and Mrs W. G. Hartley, Wattle Lane, Gisborne.</p>

<h2 class="more-heading">Check out for more views here</h2>
<div class="small-arrow" style="left:317px"><svg width="8" height="10" viewBox="0 0 8 10"><polyline points="6,1 2,5 6,9" fill="none" stroke="#000" stroke-width="2"/></svg></div>
<a class="thumb" style="left:345px;top:953px;width:40px;height:70px"><span role="img" aria-label="Portrait photograph of a couple" style="background:linear-gradient(#d8d4bc,#3a3a33)"></span></a>
<a class="thumb" style="left:396px;top:950px;width:120px;height:70px"><span role="img" aria-label="Photograph of a river bridge" style="background:linear-gradient(#e0ddc6,#7a776a)"></span></a>
<a class="thumb" style="left:532px;top:951px;width:51px;height:73px"><span role="img" aria-label="Photograph of a bride and groom" style="background:linear-gradient(#d6d3c2,#6e6c60)"></span></a>
<a class="thumb" style="left:607px;top:962px;width:85px;height:61px"><span role="img" aria-label="Portrait of a man beside a printed article" style="background:linear-gradient(90deg,#3d3d38 45%,#dcd9cb 45%)"></span></a>
<a class="thumb" style="left:702px;top:957px;width:100px;height:64px"><span role="img" aria-label="Group photograph of a sports team in blazers" style="background:linear-gradient(#cfccb8,#45443d)"></span></a>
<div class="small-arrow" style="left:806px"><svg width="8" height="10" viewBox="0 0 8 10"><polyline points="2,1 6,5 2,9" fill="none" stroke="#000" stroke-width="2"/></svg></div>

<footer class="site-footer"></footer>
<a class="social-link friendbook" href="#"><i></i>Friendbook</a>
<div class="like-us">like us</div>
<a class="social-link chirper" href="#"><i></i>Chirper</a>
<div class="licence-badge"></div>
<div class="copyright">© 2012 Kelray Heritage Library</div>

</body>
</html>
```